Harborline Renewal Business Card Design

Professional and clean design. The design colors should flow with the logo. Two-sided card with the website on the back which is:

www.HarborlineRenewal.example.

"Specializing in Water Damage Restoration"

On the front I need the name, email, phone, and logo.

Name: Darnell Quisby
Email: Darnell@HarborlineRenewal.example
Phone: 555-318-2046 for now

I only have the Preview and Thumbnail right now but should have the source files uploaded within a day or two.

Target Market(s)

Flood victims, home owners with water damage from busted pipes etc...

Industry/Entity Type

Business

Contact Information for Business Card

Name: Darnell Quisby

Font styles to use
Serif
Sans Serif

Requirements
Must have
• Business Card Details Info

```html
<!DOCTYPE html>
<html lang="en">
<head>
<meta charset="utf-8">
<title>Harborline Renewal Business Card</title>
<link rel="stylesheet" href="https://fonts.googleapis.com/css2?family=Cinzel:wght@400;600&family=Open+Sans:wght@400;600&display=swap">
<style>
  :root {
    --page-bg: #e9ebee;
    --card-white: #ffffff;
    --brand-blue: #2b93d1;
    --brand-blue-deep: #1677b8;
    --brand-blue-light: #5cb8e6;
    --wave-accent: #8fd0f0;
    --text-dark: #3a3a3a;
    --text-white: #ffffff;
  }
  * { margin: 0; padding: 0; box-sizing: border-box; }
  html, body {
    width: 1200px;
    height: 843px;
    overflow: hidden;
    background: var(--page-bg);
  }
  .canvas {
    width: 1200px;
    height: 843px;
    display: flex;
    align-items: center;
    justify-content: center;
    gap: 44px;
  }
  .card {
    position: relative;
    width: 540px;
    height: 308px;
    background: var(--card-white);
    border-radius: 16px;
    overflow: hidden;
    box-shadow: 0 6px 18px rgba(0, 0, 0, 0.12);
  }
  .brand-circle {
    border-radius: 50%;
    background: var(--brand-blue);
  }
  .brand-name {
    font-family: "Cinzel", serif;
    font-weight: 600;
    color: var(--brand-blue);
    letter-spacing: 0.06em;
    white-space: nowrap;
  }

  /* Back side */
  .card-back {
    display: flex;
    flex-direction: column;
    align-items: center;
    justify-content: center;
  }
  .card-back .brand-circle {
    width: 96px;
    height: 96px;
    margin-bottom: 18px;
  }
  .card-back .brand-name {
    font-size: 30px;
  }
  .card-back .tagline {
    margin-top: 26px;
    font-family: "Open Sans", sans-serif;
    font-weight: 600;
    font-size: 15px;
    color: var(--text-dark);
    letter-spacing: 0.02em;
  }

  /* Front side */
  .card-front .brand-lockup {
    position: absolute;
    left: 40px;
    top: 26px;
    display: flex;
    flex-direction: column;
    align-items: center;
  }
  .card-front .brand-circle {
    width: 44px;
    height: 44px;
    margin-bottom: 10px;
  }
  .card-front .brand-name {
    font-size: 24px;
  }
  .wave {
    position: absolute;
    left: 0;
    bottom: 0;
    width: 540px;
    height: 308px;
  }
  .contact-block {
    position: absolute;
    right: 30px;
    top: 178px;
    text-align: right;
    color: var(--text-white);
  }
  .person-name {
    font-family: "Cinzel", serif;
    font-weight: 400;
    font-size: 25px;
    letter-spacing: 0.05em;
    margin-bottom: 8px;
  }
  .contact-line {
    display: flex;
    align-items: center;
    justify-content: flex-end;
    gap: 12px;
    font-family: "Open Sans", sans-serif;
    font-size: 15px;
    line-height: 24px;
  }
  .contact-icon {
    width: 14px;
    height: 14px;
    flex: none;
  }
</style>
</head>
<body>
<main class="canvas">

  <section class="card card-back" aria-label="Back of business card">
    <div class="brand-circle"></div>
    <div class="brand-name">Harborline Renewal</div>
    <p class="tagline">Specializing in Water Damage Restoration</p>
  </section>

  <section class="card card-front" aria-label="Front of business card">
    <svg class="wave" viewBox="0 0 540 308" aria-hidden="true">
      <defs>
        <linearGradient id="waveFill" x1="0" y1="0" x2="1" y2="1">
          <stop offset="0" stop-color="var(--brand-blue-light)"/>
          <stop offset="0.5" stop-color="var(--brand-blue)"/>
          <stop offset="1" stop-color="var(--brand-blue-deep)"/>
        </linearGradient>
      </defs>
      <path d="M0 196 C 110 205, 200 190, 290 150 C 370 115, 450 108, 540 118 L540 308 L0 308 Z" fill="var(--wave-accent)"/>
      <path d="M0 206 C 110 214, 200 200, 292 162 C 372 128, 452 122, 540 130 L540 308 L0 308 Z" fill="#ffffff"/>
      <path d="M0 214 C 112 222, 204 208, 296 170 C 376 137, 455 131, 540 138 L540 308 L0 308 Z" fill="url(#waveFill)"/>
    </svg>

    <div class="brand-lockup">
      <div class="brand-circle"></div>
      <div class="brand-name">Harborline Renewal</div>
    </div>

    <div class="contact-block">
      <div class="person-name">Darnell Quisby</div>
      <div class="contact-line">
        <span>555-318-2046 for now</span>
        <svg class="contact-icon" viewBox="0 0 24 24" aria-hidden="true"><path fill="#fff" d="M6.6 10.8a15 15 0 0 0 6.6 6.6l2.2-2.2a1 1 0 0 1 1-.25 11.4 11.4 0 0 0 3.6.57 1 1 0 0 1 1 1V20a1 1 0 0 1-1 1A17 17 0 0 1 3 4a1 1 0 0 1 1-1h3.5a1 1 0 0 1 1 1c0 1.25.2 2.46.57 3.6a1 1 0 0 1-.25 1z"/></svg>
      </div>
      <div class="contact-line">
        <span>Darnell@HarborlineRenewal.example</span>
        <svg class="contact-icon" viewBox="0 0 24 24" aria-hidden="true"><rect x="2" y="5" width="20" height="14" rx="2" fill="#fff"/><path d="M3 6l9 7 9-7" fill="none" stroke="var(--brand-blue)" stroke-width="1.8"/></svg>
      </div>
      <div class="contact-line">
        <span>www.HarborlineRenewal.example</span>
        <svg class="contact-icon" viewBox="0 0 24 24" aria-hidden="true"><circle cx="12" cy="12" r="10" fill="#fff"/><path d="M2 12h20M12 2c3 3 3 17 0 20M12 2c-3 3-3 17 0 20" fill="none" stroke="var(--brand-blue)" stroke-width="1.4"/></svg>
      </div>
    </div>
  </section>

</main>
</body>
</html>
```